Business Card Design Project

I would like to redesign our business cards and change the look and feel of our marketing material, but maintain the same basic identity of our current logo.
It is my belief that it could be much better.
You can view our website at tkuvo.com

   

I was looking for a completely different look.  Something much more hip and cool looking.  You can change the colors.

I like this look and feel

 http://www.onbmediators.com

 But obviously don’t want to copy them exactly.

 

For the back just leave the last point.

“Focus on Your Business, and We’ll Focus on Your Claim”

I want there to be space for someone to write on.

                                                                    

                                       

I like this look and feel

 http://www.onbmediators.com

 

Marketing

```html
<!DOCTYPE html>
<html lang="en">
<head>
<meta charset="utf-8">
<title>Tkuvo Claim Partners – Business Card</title>
<link rel="stylesheet" href="https://fonts.googleapis.com/css2?family=Questrial&display=swap">
<style>
  :root {
    --backdrop: #e9ecf1;
    --card-white: #ffffff;
    --brand-orange: #f7a81b;
    --accent-orange: #f39a12;
    --tagline-red: #e2541c;
    --name-grey: #6d7079;
    --contact-blue: #5d79b5;
    --brand-blue: #1f4fa3;
  }
  * { box-sizing: border-box; margin: 0; padding: 0; }
  html, body {
    width: 1200px;
    height: 900px;
    overflow: hidden;
    background: var(--backdrop);
    font-family: "Questrial", "Century Gothic", sans-serif;
  }
  .sheet {
    position: relative;
    width: 1200px;
    height: 900px;
    display: flex;
    justify-content: center;
    align-items: center;
    gap: 80px;
  }
  .card {
    position: relative;
    width: 360px;
    height: 630px;
    overflow: hidden;
    box-shadow: 0 10px 30px rgba(30, 40, 70, 0.18);
  }

  /* Front */
  .card--front {
    background: var(--card-white);
    padding: 40px 36px 0;
  }
  .card--front::after {
    content: "";
    position: absolute;
    left: 0; right: 0; bottom: 0;
    height: 10px;
    background: var(--brand-orange);
  }
  .brand {
    display: flex;
    align-items: center;
    gap: 10px;
  }
  .brand__dot {
    width: 24px;
    height: 24px;
    border-radius: 50%;
    background: var(--brand-blue);
    flex: none;
  }
  .brand__name {
    font-size: 12px;
    letter-spacing: 0.12em;
    text-transform: uppercase;
    color: var(--accent-orange);
  }
  .holder {
    margin-top: 120px;
    font-size: 24px;
    font-weight: 400;
    letter-spacing: 0.06em;
    text-transform: uppercase;
    color: var(--name-grey);
  }
  .contact {
    margin-top: 40px;
    list-style: none;
    font-size: 17px;
    line-height: 1.65;
    letter-spacing: 0.04em;
    color: var(--contact-blue);
  }
  .address {
    margin-top: 40px;
    font-style: normal;
    font-size: 17px;
    line-height: 1.65;
    letter-spacing: 0.03em;
    color: var(--contact-blue);
  }

  /* Back */
  .card--back {
    background: var(--brand-orange);
    padding: 44px 36px;
  }
  .tagline {
    font-size: 17px;
    line-height: 1.6;
    letter-spacing: 0.1em;
    color: var(--tagline-red);
  }
  .card__disc {
    position: absolute;
    left: 20px;
    bottom: -90px;
    width: 180px;
    height: 180px;
    border-radius: 50%;
    background: var(--card-white);
  }
</style>
</head>
<body>
  <main class="sheet">
    <section class="card card--front" aria-label="Business card front">
      <header class="brand">
        <span class="brand__dot"></span>
        <span class="brand__name">Tkuvo Claim Partners</span>
      </header>
      <h1 class="holder">Daniel Whitcombe</h1>
      <ul class="contact">
        <li>office: 516-555-0148</li>
        <li>cell: 917-555-0172</li>
        <li>dw@tkuvo.com</li>
        <li>www.tkuvo.com</li>
      </ul>
      <address class="address">
        240 Linden Avenue<br>
        Westbury, NY 11590
      </address>
    </section>

    <section class="card card--back" aria-label="Business card back">
      <p class="tagline">Run Your Company Well,<br>Let Us Handle the Rest</p>
      <span class="card__disc"></span>
    </section>
  </main>
</body>
</html>
```